UI Improvement for FlorKeep app

We are looking for a talented UI/UX designer to REFINE and enhance the visual design of our mobile application, FlorKeep. The app is fully functional, but we need a designer to improve its aesthetics by specifying design elements such as fonts, colors, spacing, and component styles.
Your task will be to analyze the CURRENT UI and provide detailed design specifications that will make the app more visually appealing, modern, and user-friendly.
TODO:
Review the existing FlorKeep app design (see attachments) and identify areas for visual improvement.
Provide a detailed UI style guide, including:
Typography (font choices, sizes, and weights)
Color palette (primary, secondary, and accent colors)
Component styling (buttons, forms, icons, and interactive elements)
Spacing and layout guidelines (margins, paddings, and alignment)
Ensure the design remains clean, modern, and professional while maintaining usability and accessibility.
Provide design mockups or visual examples (if possible) to illustrate the proposed changes.
Deliverables:
A UI Style Guide (PDF or Figma file) with specifications on fonts, colors, spacing, and UI components.
Optionally, before/after mockups or examples demonstrating the improvements.
Ideal Designer:
Strong experience in mobile UI/UX design.
Understanding of modern design trends and best practices.
Ability to communicate design choices clearly for easy developer implementation.
I have attached 7 images showcasing the main UI screens used in the FlorKeep app. These screens need visual enhancements to improve their overall look and user experience.
The images represent the current design in three key modes:
LIST Mode – Displays data in a structured list format.
READ Mode – Shows detailed information when a user selects an item.
ADD/EDIT Mode – Allows users to input or modify information.
Additionally, there is a ‘MORE’ page, which serves as a menu listing other features of the application.
Task Objective:
Please refine and improve these UIs to create a more modern, visually appealing, and user-friendly experience. Focus on typography, colors, spacing, and component styling to ensure a cohesive and polished design.
Look and feel
Each slider illustrates characteristics of the customer's brand and the style your logo design should communicate.

```html
<!DOCTYPE html>
<html lang="en">
<head>
<meta charset="utf-8">
<title>FlorKeep – App Screens</title>
<link href="https://fonts.googleapis.com/css2?family=Poppins:wght@600;700&family=Roboto:wght@400;500&display=swap" rel="stylesheet">
<style>
  :root{
    --bg:#e9edf3;
    --screen:#ffffff;
    --orange:#e84c1b;
    --blue:#0b4fb3;
    --ink:#1b1b1f;
    --muted:#9a9ca3;
    --field:#f1f2f4;
    --tile:#eef3fb;
    --line:#e6e7ea;
  }
  *{box-sizing:border-box;margin:0;padding:0}
  html,body{width:1200px;height:762px;overflow:hidden}
  body{background:var(--bg);font-family:"Roboto",sans-serif;color:var(--ink);position:relative}
  .screen{position:absolute;top:95px;width:278px;height:571px;background:var(--screen);border-radius:22px;overflow:hidden;box-shadow:0 10px 30px rgba(20,30,60,.12)}
  .screen--add{left:103px}.screen--pilots{left:462px}.screen--more{left:821px}
  .status{position:absolute;top:9px;left:22px;right:22px;display:flex;justify-content:space-between;align-items:center;font-size:10px;font-weight:500}
  .brand{position:absolute;top:27px;width:100%;text-align:center;font-family:"Poppins",sans-serif;font-weight:700;font-size:12px;color:var(--orange);letter-spacing:.3px}
  .divider{position:absolute;top:48px;left:22px;right:22px;height:1px;background:var(--line)}
  .title{position:absolute;top:55px;width:100%;text-align:center;font-family:"Poppins",sans-serif;font-weight:600;font-size:12.5px}
  .back{position:absolute;top:61px;left:22px}
  .dots{position:absolute;top:63px;right:16px}
  .plus{position:absolute;top:58px;left:220px}
  .label{position:absolute;font-size:7.5px}
  .field{position:absolute;height:19px;background:var(--field);border-radius:5px;font-size:5.5px;color:var(--muted);padding-left:9px;line-height:19px}
  .search{position:absolute;top:85px;left:37px;width:206px;height:19px;border:1px solid #dcdde0;font-size:6px;color:#777;padding-left:6px;line-height:17px}
  .search-btn{position:absolute;right:-1px;top:-1px;width:14px;height:19px;background:var(--orange);display:flex;align-items:center;justify-content:center}
  .card{position:absolute;left:37px;width:206px;height:49px;border:1px solid #eeeff2;border-radius:3px;background:#fff}
  .photo{position:absolute;left:3px;top:2px;width:51px;height:44px;background:linear-gradient(160deg,#7d8a8f,#4f6b6f 60%,#3e5866)}
  .card-name{position:absolute;left:65px;top:12px;font-size:9px;font-weight:500}
  .card-meta{position:absolute;left:65px;top:28px;font-size:5.5px;display:flex;gap:9px;align-items:center}
  .card-id{color:var(--orange)}
  .card-date{color:var(--blue);display:flex;gap:3px;align-items:center}
  .tile{position:absolute;background:var(--tile);border-radius:6px;display:flex;flex-direction:column;align-items:center;justify-content:center;gap:6px;font-size:8px;height:47px}
  .tile--active{background:var(--orange);color:#fff}
  .nav{position:absolute;left:8px;right:6px;bottom:0;height:45px;background:var(--blue);border-radius:12px 12px 0 0;display:flex;overflow:hidden}
  .nav-item{display:flex;flex-direction:column;align-items:center;justify-content:center;gap:3px;color:#fff;font-size:8.5px;font-weight:500}
  .nav-item--active{background:var(--orange)}
</style>
</head>
<body>
<svg width="0" height="0" style="position:absolute">
  <defs>
    <symbol id="i-phone" viewBox="0 0 24 24"><path d="M5 3h4l2 5-3 2a12 12 0 006 6l2-3 5 2v4a2 2 0 01-2 2A18 18 0 013 5a2 2 0 012-2z" fill="currentColor"/></symbol>
    <symbol id="i-bag" viewBox="0 0 24 24"><path d="M8 6V4h8v2h5v14H3V6zm2 0h4V5h-4z" fill="currentColor"/></symbol>
    <symbol id="i-mic" viewBox="0 0 24 24"><rect x="9" y="2" width="6" height="12" rx="3" fill="currentColor"/><path d="M6 11a6 6 0 0012 0M12 17v5M8 22h8" stroke="currentColor" stroke-width="2" fill="none"/></symbol>
    <symbol id="i-grid" viewBox="0 0 24 24"><rect x="3" y="3" width="8" height="8" rx="1.5" fill="currentColor"/><rect x="13" y="3" width="8" height="8" rx="1.5" fill="currentColor"/><rect x="3" y="13" width="8" height="8" rx="1.5" fill="currentColor"/><rect x="13" y="13" width="8" height="8" rx="1.5" fill="currentColor"/></symbol>
    <symbol id="i-pilot" viewBox="0 0 24 24"><path d="M6 4l6-2 6 2-1 3H7z" fill="currentColor"/><circle cx="12" cy="10" r="3.5" fill="currentColor"/><path d="M4 22c0-5 4-7 8-7s8 2 8 7z" fill="currentColor"/></symbol>
    <symbol id="i-plane" viewBox="0 0 24 24"><path d="M2 13l4-1 3-6h3l-2 5 7-1 3-3h2l-1 5 1 5h-2l-3-3-7-1 2 5H9l-3-6-4-1z" fill="currentColor"/></symbol>
    <symbol id="i-help" viewBox="0 0 24 24"><path d="M12 2a9 9 0 019 9c0 5-4 8-9 8l-3 3v-4a9 9 0 013-16z" fill="currentColor"/><path d="M9.5 9a2.5 2.5 0 115 0c0 2-2.5 2-2.5 4" stroke="#0b4fb3" stroke-width="1.8" fill="none"/><circle cx="12" cy="15.5" r="1" fill="#0b4fb3"/></symbol>
    <symbol id="i-dots" viewBox="0 0 20 6"><circle cx="3" cy="3" r="2.5" fill="currentColor"/><circle cx="10" cy="3" r="2.5" fill="currentColor"/><circle cx="17" cy="3" r="2.5" fill="currentColor"/></symbol>
    <symbol id="i-cal" viewBox="0 0 24 24"><path d="M3 5h18v16H3z" fill="none" stroke="currentColor" stroke-width="2"/><path d="M3 5h18v4H3zM7 2v4M17 2v4" stroke="currentColor" stroke-width="2" fill="currentColor"/><path d="M7 12h2v2H7zm4 0h2v2h-2zm4 0h2v2h-2zM7 16h2v2H7zm4 0h2v2h-2z" fill="currentColor"/></symbol>
  </defs>
</svg>

<!-- Add Contact -->
<section class="screen screen--add">
  <div class="status"><span>12:00</span><span>▮▮ ◔ ▭</span></div>
  <div class="brand">FLORKEEP</div>
  <div class="divider"></div>
  <svg class="back" width="12" height="8" viewBox="0 0 12 8"><path d="M11 4H2M4.5 1L1.5 4l3 3" stroke="#0b4fb3" stroke-width="1.6" fill="none"/></svg>
  <div class="title">Add Contact</div>
  <svg class="dots" width="16" height="5" style="color:var(--blue)"><use href="#i-dots"/></svg>

  <div class="label" style="top:106px;left:22px">Business Name</div>
  <div class="field" style="top:115px;left:22px;width:113px">lorem ipsum</div>
  <div class="label" style="top:106px;left:144px">First Name</div>
  <div class="field" style="top:115px;left:144px;width:113px">lorem ipsum</div>

  <div class="label" style="top:149px;left:22px">Middle Name</div>
  <div class="field" style="top:158px;left:22px;width:113px">lorem ipsum</div>
  <div class="label" style="top:149px;left:144px">Last Name</div>
  <div class="field" style="top:158px;left:144px;width:113px">lorem ipsum</div>

  <div class="label" style="top:193px;left:22px">Address Label Tag - e</div>
  <div class="field" style="top:202px;left:22px;width:235px">lorem ipsum</div>
  <div class="label" style="top:237px;left:22px">Address Line 1 - e</div>
  <div class="field" style="top:246px;left:22px;width:235px">lorem ipsum</div>
  <div class="label" style="top:280px;left:22px">Address Line 2 - e</div>
  <div class="field" style="top:289px;left:22px;width:235px">lorem ipsum</div>
  <div class="label" style="top:321px;left:22px">Address City</div>
  <div class="field" style="top:330px;left:22px;width:235px">City</div>
  <div class="label" style="top:365px;left:22px">Address State</div>
  <div class="field" style="top:374px;left:22px;width:235px">Lorem Ipsum</div>
  <div class="label" style="top:408px;left:22px">ZIP - e</div>
  <div class="field" style="top:417px;left:22px;width:235px">lorem ipsum</div>

  <nav class="nav">
    <div class="nav-item nav-item--active" style="width:65px"><svg width="15" height="15"><use href="#i-phone"/></svg>Contact</div>
    <div class="nav-item" style="width:85px"><svg width="15" height="15"><use href="#i-bag"/></svg>Work Order</div>
    <div class="nav-item" style="width:60px"><svg width="15" height="15"><use href="#i-mic"/></svg>Invoice</div>
    <div class="nav-item" style="width:54px"><svg width="15" height="15"><use href="#i-grid"/></svg>More</div>
  </nav>
</section>

<!-- Pilots list -->
<section class="screen screen--pilots">
  <div class="status"><span>12:00</span><span>▮▮ ◔ ▭</span></div>
  <div class="brand">FLORKEEP</div>
  <div class="divider"></div>
  <div class="title">Pilots</div>
  <svg class="plus" width="11" height="11" viewBox="0 0 11 11"><rect width="11" height="11" rx="2" fill="#0b4fb3"/><path d="M5.5 2.5v6M2.5 5.5h6" stroke="#fff" stroke-width="1.6"/></svg>
  <svg class="dots" width="16" height="5" style="color:var(--blue)"><use href="#i-dots"/></svg>
  <div class="search">Search<span class="search-btn"><svg width="8" height="8" viewBox="0 0 10 10"><circle cx="4" cy="4" r="3" stroke="#fff" stroke-width="1.5" fill="none"/><path d="M6.3 6.3L9 9" stroke="#fff" stroke-width="1.5"/></svg></span></div>

  <div class="card" style="top:123px"><div class="photo" role="img" aria-label="Pilot profile photo"></div><div class="card-name">Moreno,Daniel,Scott</div><div class="card-meta"><span class="card-id">40527718</span><span class="card-date"><svg width="6" height="6"><use href="#i-cal"/></svg>9/30/24</span></div></div>
  <div class="card" style="top:179px"><div class="photo" role="img" aria-label="Pilot profile photo"></div><div class="card-name">Moreno,Daniel,Scott</div><div class="card-meta"><span class="card-id">40527718</span><span class="card-date"><svg width="6" height="6"><use href="#i-cal"/></svg>9/30/24</span></div></div>
  <div class="card" style="top:235px"><div class="photo" role="img" aria-label="Pilot profile photo"></div><div class="card-name">Moreno,Daniel,Scott</div><div class="card-meta"><span class="card-id">40527718</span><span class="card-date"><svg width="6" height="6"><use href="#i-cal"/></svg>9/30/24</span></div></div>
  <div class="card" style="top:291px"><div class="photo" role="img" aria-label="Pilot profile photo"></div><div class="card-name">Moreno,Daniel,Scott</div><div class="card-meta"><span class="card-id">40527718</span><span class="card-date"><svg width="6" height="6"><use href="#i-cal"/></svg>9/30/24</span></div></div>
  <div class="card" style="top:347px"><div class="photo" role="img" aria-label="Pilot profile photo"></div><div class="card-name">Moreno,Daniel,Scott</div><div class="card-meta"><span class="card-id">40527718</span><span class="card-date"><svg width="6" height="6"><use href="#i-cal"/></svg>9/30/24</span></div></div>
  <div class="card" style="top:403px"><div class="photo" role="img" aria-label="Pilot profile photo"></div><div class="card-name">Moreno,Daniel,Scott</div><div class="card-meta"><span class="card-id">40527718</span><span class="card-date"><svg width="6" height="6"><use href="#i-cal"/></svg>9/30/24</span></div></div>
  <div class="card" style="top:459px"><div class="photo" role="img" aria-label="Pilot profile photo"></div><div class="card-name">Moreno,Daniel,Scott</div><div class="card-meta"><span class="card-id">40527718</span><span class="card-date"><svg width="6" height="6"><use href="#i-cal"/></svg>9/30/24</span></div></div>

  <nav class="nav">
    <div class="nav-item" style="width:59px"><svg width="15" height="15"><use href="#i-phone"/></svg>Contact</div>
    <div class="nav-item nav-item--active" style="width:40px"><svg width="15" height="15"><use href="#i-pilot"/></svg>Pilot</div>
    <div class="nav-item" style="width:45px"><svg width="16" height="15"><use href="#i-plane"/></svg>Plane</div>
    <div class="nav-item" style="width:65px"><svg width="15" height="15"><use href="#i-help"/></svg>Flt Request</div>
    <div class="nav-item" style="width:55px"><svg width="15" height="15"><use href="#i-grid"/></svg>More</div>
  </nav>
</section>

<!-- More menu -->
<section class="screen screen--more">
  <div class="status"><span>12:00</span><span>▮▮ ◔ ▭</span></div>
  <div class="brand">FLORKEEP</div>
  <div class="divider"></div>
  <div class="title">More</div>
  <svg class="dots" width="16" height="5" style="color:var(--blue)"><use href="#i-dots"/></svg>

  <div class="tile" style="top:102px;left:36px;width:60px"><svg width="11" height="11" style="color:var(--blue)"><use href="#i-plane"/></svg>Flight</div>
  <div class="tile" style="top:102px;left:109px;width:60px"><svg width="11" height="11" viewBox="0 0 12 12"><rect x="2" y="5" width="8" height="7" rx="1" fill="#0b4fb3"/><path d="M3.8 5V3.5a2.2 2.2 0 014.4 0V5" stroke="#0b4fb3" stroke-width="1.4" fill="none"/></svg>Login</div>
  <div class="tile" style="top:102px;left:183px;width:60px"><svg width="11" height="11" viewBox="0 0 12 12"><circle cx="6" cy="3.3" r="2.8" fill="#0b4fb3"/><path d="M1 12c0-3.5 2.3-5 5-5s5 1.5 5 5z" fill="#0b4fb3"/></svg>Account</div>

  <div class="tile" style="top:161px;left:36px;width:60px"><svg width="11" height="11" style="color:var(--blue)"><use href="#i-cal"/></svg>Calender</div>
  <div class="tile tile--active" style="top:161px;left:109px;width:60px"><svg width="12" height="12" viewBox="0 0 12 12"><circle cx="6" cy="6" r="5.2" stroke="#fff" stroke-width="1.3" fill="none"/><circle cx="6" cy="4.8" r="1.8" fill="#fff"/><path d="M2.8 9.6c.8-1.4 1.9-2 3.2-2s2.4.6 3.2 2" stroke="#fff" stroke-width="1.3" fill="none"/></svg>Users</div>
  <div class="tile" style="top:161px;left:183px;width:60px"><svg width="13" height="11" viewBox="0 0 13 11"><rect x=".7" y=".7" width="11.6" height="9.6" rx="1" stroke="#0b4fb3" stroke-width="1.2" fill="none"/><path d="M.7 3h11.6M3 5.5h7M3 7.8h7" stroke="#0b4fb3" stroke-width="1.1"/></svg>Dashboard</div>

  <div class="tile" style="top:220px;left:36px;width:97px"><svg width="9" height="12" viewBox="0 0 9 12"><path d="M4.5 0A4.5 4.5 0 000 4.5C0 8 4.5 12 4.5 12S9 8 9 4.5A4.5 4.5 0 004.5 0zm0 6.2a1.7 1.7 0 110-3.4 1.7 1.7 0 010 3.4z" fill="#0b4fb3"/></svg>Tracking</div>
  <div class="tile" style="top:220px;left:145px;width:97px"><svg width="12" height="12" viewBox="0 0 12 12"><rect x="1" y="4" width="10" height="3" fill="#0b4fb3"/><rect x="2" y="7" width="8" height="5" fill="#0b4fb3"/><path d="M6 4V12" stroke="#eef3fb" stroke-width="1"/><path d="M6 4C4 1 2 2 3.5 4M6 4c2-3 4-2 2.5 0" stroke="#0b4fb3" stroke-width="1.2" fill="none"/></svg>Outreach Event</div>

  <div class="tile" style="top:276px;left:36px;width:97px"><svg width="13" height="11" style="color:var(--blue)"><use href="#i-bag"/></svg>Maintenance Resource</div>
  <div class="tile" style="top:276px;left:145px;width:97px"><svg width="12" height="12" viewBox="0 0 24 24"><path d="M10 1h4l.6 3 2.4 1 2.6-1.7 2.8 2.8L20.7 8.7l1 2.3 3 .6v4l-3 .6-1 2.4 1.7 2.6-2.8 2.8-2.6-1.7-2.4 1-.6 3h-4l-.6-3-2.4-1-2.6 1.7-2.8-2.8 1.7-2.6-1-2.4-3-.6v-4l3-.6 1-2.3L1.6 6.1l2.8-2.8L7 5l2.4-1z" fill="#0b4fb3" transform="scale(.92) translate(1 0)"/><circle cx="12" cy="12" r="3.5" fill="#eef3fb"/></svg>Settings</div>

  <nav class="nav">
    <div class="nav-item" style="width:66px"><svg width="15" height="15"><use href="#i-phone"/></svg>Contact</div>
    <div class="nav-item" style="width:42px"><svg width="15" height="15"><use href="#i-pilot"/></svg>Pilot</div>
    <div class="nav-item" style="width:46px"><svg width="16" height="15"><use href="#i-plane"/></svg>Plane</div>
    <div class="nav-item" style="width:64px"><svg width="15" height="15"><use href="#i-help"/></svg>Flt Request</div>
    <div class="nav-item nav-item--active" style="width:46px"><svg width="15" height="15"><use href="#i-grid"/></svg>More</div>
  </nav>
</section>
</body>
</html>
```